dsadasdasdasdsa

Industry/Entity Type

Mortgage Broking

Requirements
Must have
• Call-to-action button somewhere on the graphic
Nice to have
• The font of our logo is Montserrat

```html
<!DOCTYPE html>
<html lang="en">
<head>
<meta charset="UTF-8">
<title>Mortgage Broker Directory Banner</title>
<link rel="stylesheet" href="https://fonts.googleapis.com/css2?family=Montserrat:wght@600;800;900&display=swap">
<style>
  :root {
    --red-bright: #e0452f;
    --green-text: #1d5c3c;
    --yellow: #f7e81c;
    --white: #ffffff;
    --button-red: #c9301f;
  }
  * { margin: 0; padding: 0; box-sizing: border-box; }
  html, body { width: 1200px; height: 180px; overflow: hidden; background: var(--white); }
  .banner {
    position: relative;
    width: 1200px;
    height: 180px;
    overflow: hidden;
    font-family: "Montserrat", sans-serif;
  }
  .banner-backdrop { position: absolute; inset: 0; }
  .cta-button {
    position: absolute;
    left: 29px;
    top: 70px;
    width: 244px;
    height: 58px;
    border: 4px solid var(--yellow);
    border-radius: 30px;
    background: var(--button-red);
    color: var(--white);
    font-weight: 900;
    font-size: 24px;
    letter-spacing: 0.3px;
    display: flex;
    align-items: center;
    justify-content: center;
    text-decoration: none;
    white-space: nowrap;
    z-index: 2;
  }
  .mascot-area {
    position: absolute;
    left: 300px;
    top: 0;
    width: 165px;
    height: 180px;
    border-radius: 48% 48% 30% 30%;
    background: radial-gradient(ellipse at 50% 35%, #7ccf5c 0%, #4fa63f 50%, #8a5a2e 100%);
    z-index: 1;
  }
  .headline-question {
    position: absolute;
    right: 28px;
    top: 18px;
    color: var(--yellow);
    font-weight: 600;
    font-size: 27px;
    white-space: nowrap;
  }
  .directory-lines {
    position: absolute;
    right: 28px;
    top: 77px;
    text-align: right;
    font-weight: 900;
    text-transform: uppercase;
    line-height: 1;
    white-space: nowrap;
  }
  .directory-lines .line-top { font-size: 36px; color: var(--green-text); letter-spacing: 0.2px; }
  .directory-lines .line-top .accent { color: var(--red-bright); }
  .directory-lines .line-bottom { font-size: 48px; color: var(--green-text); margin-top: 2px; }
</style>
</head>
<body>
<div class="banner">
  <svg class="banner-backdrop" width="1200" height="180" viewBox="0 0 1200 180" aria-hidden="true">
    <defs>
      <radialGradient id="redGlow" cx="300" cy="90" r="380" gradientUnits="userSpaceOnUse">
        <stop offset="0" stop-color="#ff6b3d"/>
        <stop offset="0.5" stop-color="#d8362a"/>
        <stop offset="1" stop-color="#a81d18"/>
      </radialGradient>
      <radialGradient id="greenGlow" cx="380" cy="90" r="900" gradientUnits="userSpaceOnUse">
        <stop offset="0" stop-color="#2fa356"/>
        <stop offset="0.5" stop-color="#1a7a3c"/>
        <stop offset="1" stop-color="#0c4d25"/>
      </radialGradient>
    </defs>
    <rect class="backdrop-green" width="1200" height="180" fill="url(#greenGlow)"/>
    <g class="backdrop-green-rays" fill="#ffffff" opacity="0.06">
      <polygon points="380,90 720,0 830,0"/>
      <polygon points="380,90 980,0 1100,0"/>
      <polygon points="380,90 1200,30 1200,70"/>
    </g>
    <polygon class="backdrop-red" points="0,0 383,0 336,180 0,180" fill="url(#redGlow)"/>
    <g class="backdrop-red-rays" fill="#ffffff" opacity="0.07">
      <polygon points="330,90 0,0 60,0"/>
      <polygon points="330,90 0,60 0,110"/>
      <polygon points="330,90 80,180 20,180"/>
      <polygon points="330,90 200,0 250,0"/>
    </g>
    <polygon class="directory-band" points="470,70 1200,70 1200,180 458,180" fill="#ffffff"/>
  </svg>

  <a class="cta-button" href="#">CLICK HERE</a>

  <div class="mascot-area" role="img" aria-label="Smiling cartoon turtle mascot"></div>

  <p class="headline-question">Need a Mortgage Broker?</p>

  <div class="directory-lines">
    <p class="line-top"><span class="accent">Search Now</span> on Australia’s</p>
    <p class="line-bottom">Largest Directory</p>
  </div>
</div>
</body>
</html>
```